Brightarc Orthodontics appointment card design

I need appointment cards/ business cards made. Front will be Logo, name, title, email, phone number and location (5263 Walnut Hollow Pkwy, Ste 412, Concord, NC 28027) . the back should have an appointment card (name, time, date) and also 3 addresses listed with a check box so we can check to which location they are going.
Dale Fenwick Orthodontics
- 6735 Orchard Street, Ste 514, Harrisburg, NC 28075
- 3647 Ridgeway Drive NE, Ste 810, Concord, NC 28025
- 2917 Thornbury Corporate Drive, Ste 605, Charlotte, NC 28277
Business card can be horizontal or vertical in Design.
I need to be able to edit it to update and add new employees

Requirements
Must have
• Front:
• - Logo
• - Name & Title (able to be edited)
• - phone (704-555-0186) & Email (need to be able to edit)
• - Address: 5263 Walnut Hollow Pkwy, Ste 412
• Concord, NC 28027
• Back:
• Appointment Card design:
• - Name, time, Date
• - 3 locations w/ a check box so the patient knows where to go:
• Dale Fenwick Orthodontics
• - 6735 Orchard Street, Ste 514, Harrisburg, NC 28075
• - 3647 Ridgeway Drive NE, Ste 810, Concord, NC 28025
• - 2917 Thornbury Corporate Drive, Ste 605, Charlotte, NC 28277

```html
<!DOCTYPE html>
<html lang="en">
<head>
<meta charset="utf-8">
<title>Brightarc Orthodontics – Appointment &amp; Business Card</title>
<link href="https://fonts.googleapis.com/css2?family=Roboto:wght@400;500;700&display=swap" rel="stylesheet">
<style>
  :root{
    --bg:#3a3b3d;
    --card:#ffffff;
    --blue:#1a7cc1;
    --blue-light:#2a92d6;
    --grey:#7d7f82;
    --text:#3c3c3c;
    --line:#4a4a4a;
  }
  *{margin:0;padding:0;box-sizing:border-box}
  html,body{width:1200px;height:1000px;overflow:hidden}
  body{background:var(--bg);font-family:'Roboto',Arial,sans-serif;color:var(--text);position:relative}

  .card{position:absolute;left:220px;width:760px;height:420px;background:var(--card);border-radius:26px;overflow:hidden}
  .card--back{top:50px}
  .card--front{top:530px}

  /* back side */
  .back-band{position:absolute;inset:0;pointer-events:none}
  .appt-title{position:absolute;left:40px;top:40px;font-size:24px;font-weight:700;color:var(--blue)}
  .field{position:absolute;display:flex;align-items:flex-end;font-size:15px;color:#555}
  .field .rule{flex:1;border-bottom:1.5px solid var(--line);margin-left:8px;height:1px}
  .field--name{left:40px;top:100px;width:420px}
  .field--date{left:40px;top:150px;width:680px}
  .field--time{left:40px;top:200px;width:680px}
  .field--time .rule:first-child{margin-left:0;margin-right:8px}
  .ampm{position:absolute;right:40px;top:232px;display:flex;gap:18px;font-size:15px;color:#555}
  .box{display:inline-block;width:15px;height:15px;border:1.5px solid var(--blue);margin-right:6px;vertical-align:-2px}
  .brand-back{position:absolute;right:40px;top:92px;font-size:30px;font-weight:700;color:var(--blue);text-align:right;line-height:1.1}
  .practice{position:absolute;left:0;right:0;top:270px;text-align:center;font-size:15px;color:#555}
  .practice strong{font-size:22px;color:var(--blue);font-weight:700;margin-right:4px}
  .locations{position:absolute;left:40px;right:40px;top:315px;display:flex;justify-content:space-between}
  .location{width:210px;text-align:center;font-size:13.5px;line-height:1.35;color:#555}
  .location .box{display:block;margin:0 auto 8px}

  /* front side */
  .front-swoosh{position:absolute;inset:0;pointer-events:none}
  .brand-front{position:absolute;left:50px;top:120px;width:300px;font-size:44px;font-weight:700;color:var(--blue);line-height:1.05}
  .divider{position:absolute;left:390px;top:110px;width:2px;height:150px;background:var(--blue)}
  .contact{position:absolute;left:412px;top:112px;font-size:16px;line-height:1.35;color:var(--text)}
  .contact .person{font-size:24px;font-weight:700;color:var(--blue);letter-spacing:.5px}
  .contact .role{margin-bottom:14px}
  .contact .row{display:flex;align-items:center;gap:8px;margin-top:4px}
  .contact svg{width:14px;height:14px;fill:var(--blue);flex:none}
</style>
</head>
<body>

<section class="card card--back" aria-label="Appointment card">
  <svg class="back-band" viewBox="0 0 760 420" preserveAspectRatio="none" aria-hidden="true">
    <path d="M560 0 H760 V70 C740 40 700 28 560 0 Z" fill="var(--blue)"/>
  </svg>
  <h2 class="appt-title">Next Appointment</h2>
  <div class="field field--name">Name<span class="rule"></span></div>
  <div class="field field--date">Date<span class="rule"></span></div>
  <div class="field field--time"><span class="rule"></span>Time<span class="rule"></span></div>
  <div class="ampm"><span><span class="box"></span>AM</span><span><span class="box"></span>PM</span></div>
  <div class="brand-back">Brightarc<br>Orthodontics</div>
  <p class="practice"><strong>Dale Fenwick</strong>Orthodontics</p>
  <div class="locations">
    <p class="location"><span class="box"></span>6735 Orchard Street, Ste 514,<br>Harrisburg, NC 28075</p>
    <p class="location"><span class="box"></span>3647 Ridgeway Drive NE, Ste 810,<br>Concord, NC 28025</p>
    <p class="location"><span class="box"></span>2917 Thornbury Corporate Drive,<br>Ste 605, Charlotte, NC 28277</p>
  </div>
</section>

<section class="card card--front" aria-label="Business card">
  <svg class="front-swoosh" viewBox="0 0 760 420" preserveAspectRatio="none" aria-hidden="true">
    <path d="M0 280 C120 330 220 395 340 420 H0 Z" fill="var(--grey)"/>
    <path d="M0 300 C140 345 260 400 360 420 H0 Z" fill="#fff"/>
    <path d="M0 310 C160 365 320 420 760 345 V420 H0 Z" fill="var(--blue)"/>
  </svg>
  <div class="brand-front">Brightarc<br>Orthodontics</div>
  <div class="divider"></div>
  <div class="contact">
    <div class="person">DALE FENWICK</div>
    <div class="role">Orthodontics</div>
    <div>5263 Walnut Hollow Pkwy,<br>Ste 412 - Concord, NC 28027</div>
    <div class="row">
      <svg viewBox="0 0 24 24"><path d="M6.6 10.8a15.1 15.1 0 0 0 6.6 6.6l2.2-2.2a1 1 0 0 1 1-.25 11.4 11.4 0 0 0 3.6.57 1 1 0 0 1 1 1V20a1 1 0 0 1-1 1A17 17 0 0 1 3 4a1 1 0 0 1 1-1h3.5a1 1 0 0 1 1 1c0 1.25.2 2.45.57 3.57a1 1 0 0 1-.25 1z"/></svg>
      <span>704-555-0186</span>
    </div>
    <div class="row">
      <svg viewBox="0 0 24 24"><path d="M2 5h20v14H2z M4 7v.5l8 5 8-5V7l-8 5z" fill-rule="evenodd"/></svg>
      <span>dalefenwick@brightarcmail.com</span>
    </div>
  </div>
</section>

</body>
</html>
```